Advanced Therapeutic Massage Therapist

I need a business card advertising my massage services as an advanced therapeutic massage therapist. I offer advanced therapeutic massage, swedish and deep tissue. I want to create a simple, professional and feminine card. I like bright colours and creativity.

I prefer a bold and experimental approach rather than something status-quo. A card to suggest therapeutic healing through dynamic massage. Motifs, shapes or layout which suggest movement and flow.
Updates

Target Market(s)

Everybody!

Industry/Entity Type

Health And Wellness

Contact Information for Business Card

The card should include:
My name, logo, services offered and my contact details.

Sláine Dunleavy
Massage Therapist

- Swedish - Deep Tissue - Advanced Therapeutic

Phone: (+353) 87 216 4093
Email: regenerate@slainedunleavy-example.com
Website: www.slainedunlevy-example.com

Font styles to use
Serif
Sans Serif
Decorative
Script

Colors

Designer to choose colors to be used in the design.

Requirements
Must have
• An example may contain something like this, yet concise:
• "Sláine Dunleavy
• Massage Therapist
• - Swedish - Deep Tissue - Advanced Therapeutic"
Nice to have
• This sentence is optional:
• Imagery such as a logo or symbol. I have attached a file containing a logo I had produced however the name is incorrect now as it is "Sláine" not "Nelly". It could be edited to change it to Sláine.
• I have sent the file as .psd .jpg. .pdf and .png
• I like when the card conveys energy, movement, pressure points, flow etc.
• I just like the designer to follow their own style and ideas. I like bright colours but must have a lot of a base colour to offset it. I really prefer them to follow their own inspiration. That is my preference.
Should not have
• Pine trees, non-native trees to Britain and Ireland, exotic flowers or animals that are not native to Britain and Ireland.
• I don't like brown as the background colour of the card.
• The cars shouldn't look like a wedding invitation i.e too many floral type designs.

```html
<!DOCTYPE html>
<html lang="en">
<head>
<meta charset="utf-8">
<title>Sláine Dunleavy – Massage Therapist Business Cards</title>
<link rel="stylesheet" href="https://fonts.googleapis.com/css2?family=Great+Vibes&family=Work+Sans:wght@300;400;600&display=swap">
<style>
  :root {
    --backdrop: #e9e6e1;
    --charcoal: #3a3a3b;
    --charcoal-faint: #454546;
    --gold: #c9962f;
    --gold-soft: #d9b46a;
    --mint: #9fd3c4;
    --paper: #ffffff;
    --ink: #4a4a4a;
    --ink-light: #9a9a9a;
    --beige-faint: #efe6da;
  }
  * { margin: 0; padding: 0; box-sizing: border-box; }
  html, body { width: 1200px; height: 900px; overflow: hidden; }
  body { background: var(--backdrop); font-family: "Work Sans", Arial, sans-serif; position: relative; }

  .card { position: absolute; width: 620px; height: 360px; overflow: hidden; box-shadow: 0 10px 30px rgba(0,0,0,.18); }

  /* Front: dark card, rounded on the left */
  .card--front { left: 90px; top: 70px; background: var(--charcoal); border-radius: 180px 0 0 180px; }
  .front__emblem-faint { position: absolute; left: 40px; top: 40px; width: 280px; height: 280px; border-radius: 50%; border: 2px solid var(--charcoal-faint); }
  .front__logo { position: absolute; left: 392px; top: 26px; width: 156px; height: 156px; border-radius: 50%; background: radial-gradient(circle, #bfe6da 0%, var(--mint) 70%); border: 4px solid var(--gold-soft); }
  .front__text { position: absolute; right: 30px; top: 188px; width: 380px; text-align: right; }
  .front__name { font-family: "Great Vibes", cursive; color: var(--gold); font-size: 50px; line-height: 1; }
  .front__role { color: var(--gold); font-weight: 300; font-size: 17px; letter-spacing: 2px; margin-top: 2px; }
  .front__blurb { color: var(--ink-light); font-size: 11px; line-height: 1.45; margin-top: 12px; }
  .front__services { color: var(--ink-light); font-size: 11px; margin-top: 16px; }

  /* Back: white card, rounded on the right */
  .card--back { left: 490px; top: 470px; background: var(--paper); border-radius: 0 180px 180px 0; }
  .back__emblem-faint { position: absolute; right: 30px; top: 30px; width: 300px; height: 300px; border-radius: 50%; border: 2px solid var(--beige-faint); background: radial-gradient(circle, rgba(239,230,218,.35), rgba(239,230,218,0) 70%); }
  .back__details { position: absolute; left: 40px; top: 70px; }
  .back__name { color: var(--gold); font-weight: 600; font-size: 28px; letter-spacing: .5px; }
  .back__role { color: var(--ink); font-size: 14px; letter-spacing: .5px; margin-top: 2px; }
  .contact { list-style: none; margin-top: 14px; }
  .contact__item { display: flex; align-items: center; gap: 10px; color: var(--ink); font-size: 17px; line-height: 1.5; }
  .contact__icon { width: 14px; height: 14px; flex: none; }
  .back__services { position: absolute; left: 40px; bottom: 44px; color: var(--ink); font-size: 21px; letter-spacing: .5px; }
  .sep { color: var(--gold); margin: 0 6px; }
</style>
</head>
<body>

<section class="card card--front">
  <div class="front__emblem-faint"></div>
  <div class="front__logo" aria-label="Sláine Dunleavy emblem"></div>
  <div class="front__text">
    <p class="front__name">Sláine Dunleavy</p>
    <p class="front__role">massage therapist</p>
    <p class="front__blurb">HTCB qualified specialising in advanced<br>therapeutic and deep tissue massage.</p>
    <p class="front__services">Swedish | Deep Tissue | Advanced Therapeutic</p>
  </div>
</section>

<section class="card card--back">
  <div class="back__emblem-faint"></div>
  <div class="back__details">
    <h1 class="back__name">SLÁINE DUNLEAVY</h1>
    <p class="back__role">MASSAGE THERAPIST</p>
    <ul class="contact">
      <li class="contact__item">
        <svg class="contact__icon" viewBox="0 0 24 24"><path fill="#c9962f" d="M6.6 10.8a15.1 15.1 0 0 0 6.6 6.6l2.2-2.2c.3-.3.7-.4 1-.2 1.1.4 2.3.6 3.6.6.6 0 1 .4 1 1V20c0 .6-.4 1-1 1A17 17 0 0 1 3 4c0-.6.4-1 1-1h3.5c.6 0 1 .4 1 1 0 1.3.2 2.5.6 3.6.1.3 0 .7-.2 1z"/></svg>
        <span>(+353) 87 216 4093</span>
      </li>
      <li class="contact__item">
        <svg class="contact__icon" viewBox="0 0 24 24"><rect x="2" y="5" width="20" height="14" rx="1" fill="none" stroke="#c9962f" stroke-width="2"/><path d="M2 6l10 7 10-7" fill="none" stroke="#c9962f" stroke-width="2"/></svg>
        <span>slainemassage@example.com</span>
      </li>
    </ul>
  </div>
  <p class="back__services">Swedish<span class="sep">|</span>Deep<span class="sep">|</span>Tissue<span class="sep">|</span>Advanced<span class="sep">|</span>Therapeutic</p>
</section>

</body>
</html>
```